Förderverein einer Kirchengemeinde sucht Flyer-Design
Zielgruppe
Wir sind ein Förderverein einer Kirchengemeinde, der sich für die kirchenmusikalische Arbeit einsetzt.
Wir wünschen uns ein niveauvolles und zeitgemäßes/modernes Flyerdesign, das die etablierten Konzertbesucher anspricht, aber vor allem auch Menschen erreicht und überzeugt, die (noch) nichts mit Kirche zu tun haben.
Das Alter der (Haupt-) Zielgruppe (Männer und Frauen) erstreckt sich von 45 bis 70 Jahren.
Aufgabenstellung
Bei der Wahl des Formates würden wir (aus der Sicht von Laien) ein zweimal gefaltetes DIN A4 quer Format nehmen. Aber wir lassen uns gerne überraschen und sind grundsätzlich für andere Lösungen offen.
Bitte den Abschnitt für Adress- und sonstige Dateneintragungen samt Kontodaten so gestalten und platzieren, dass man ihn leicht abtrennen und verschicken kann.
Der Flyer soll Kirchenmusik als lebendig und attraktiv darstellen und neue (jüngere) Mitglieder für den Freundeskreis werben.
Lassen Sie die Bilder sprechen!!

```html
<!DOCTYPE html>
<html lang="de">
<head>
<meta charset="utf-8">
<title>Förderkreis Tonwerk – Flyer Titel</title>
<link rel="stylesheet" href="https://fonts.googleapis.com/css2?family=Jost:wght@500&display=swap">
<style>
  :root {
    --red: #b3181f;
    --red-dark: #9c1419;
    --white: #ffffff;
    --silver: #9a9c94;
    --silver-light: #c9cbc4;
    --pipe-dark: #2a2622;
    --gold: #c9a13a;
  }
  html, body {
    margin: 0;
    padding: 0;
    width: 1200px;
    height: 846px;
    overflow: hidden;
    background: var(--white);
  }
  .flyer-cover {
    position: relative;
    width: 1200px;
    height: 846px;
    overflow: hidden;
    font-family: "Jost", "Futura", sans-serif;
  }
  .cover-photo {
    position: absolute;
    inset: 0;
    background:
      linear-gradient(180deg, rgba(0,0,0,0) 0%, rgba(0,0,0,0) 68%, rgba(201,161,58,0.85) 82%, #d9b659 92%, #efe8d6 100%),
      linear-gradient(90deg, #b89336 0%, #d4ad4a 9%, var(--silver) 14%, var(--silver-light) 24%, #7f817a 32%, var(--silver-light) 40%, var(--silver) 47%, var(--pipe-dark) 54%, var(--silver) 60%, #6d6f68 68%, var(--pipe-dark) 76%, #4a4640 100%);
  }
  .cover-panel {
    position: absolute;
    inset: 0;
    width: 1200px;
    height: 846px;
  }
  .cover-headline {
    position: absolute;
    left: 170px;
    top: 330px;
    margin: 0;
    font-weight: 500;
    font-size: 42px;
    letter-spacing: 0.2px;
    color: var(--white);
    white-space: nowrap;
  }
  .club-mark {
    position: absolute;
    left: 872px;
    top: 470px;
    width: 30px;
    height: 30px;
    border-radius: 50%;
    background: var(--white);
  }
  .club-name {
    position: absolute;
    left: 872px;
    top: 668px;
    margin: 0;
    font-weight: 500;
    font-size: 30px;
    line-height: 40px;
    letter-spacing: 2px;
    text-transform: uppercase;
    color: var(--white);
  }
</style>
</head>
<body>
  <main class="flyer-cover">
    <div class="cover-photo" role="img" aria-label="Nahaufnahme silberner Orgelpfeifen mit vergoldetem, geschnitztem Barock-Ornament"></div>

    <svg class="cover-panel" viewBox="0 0 1200 846" aria-hidden="true">
      <defs>
        <linearGradient id="panelRed" x1="0" y1="0" x2="0" y2="1">
          <stop offset="0" stop-color="var(--red-dark)"/>
          <stop offset="1" stop-color="var(--red)"/>
        </linearGradient>
      </defs>
      <polygon points="948,0 1200,0 1200,846 752,846" fill="rgba(255,255,255,0.22)"/>
      <polygon points="962,0 1200,0 1200,846 766,846" fill="url(#panelRed)"/>
    </svg>

    <h1 class="cover-headline">Kirchenmusik braucht Freunde…</h1>

    <span class="club-mark" aria-hidden="true"></span>
    <p class="club-name">Förderkreis<br>Tonwerk</p>
  </main>
</body>
</html>
```